Frostvale Harborline LLC

we need a business card design

Industry/Entity Type

hvac

Contact Information for Business Card

my logo

Requirements
Must have
• my logo and same colors

```html
<!DOCTYPE html>
<html lang="en">
<head>
<meta charset="utf-8">
<title>Frostvale Harborline LLC – Business Card</title>
<link href="https://fonts.googleapis.com/css2?family=Montserrat:wght@400;500;600;700&display=swap" rel="stylesheet">
<style>
  :root {
    --navy: #0b5aa6;
    --sky: #0ab0e0;
    --sun: #f6b851;
    --ink: #1c1c1c;
    --paper: #ffffff;
    --backdrop: #ebebed;
  }
  * { margin: 0; padding: 0; box-sizing: border-box; }
  html, body {
    width: 1200px; height: 1108px; overflow: hidden;
    background: var(--backdrop);
    font-family: "Montserrat", sans-serif;
  }
  .canvas { position: relative; width: 1200px; height: 1108px; }

  .card { position: absolute; overflow: hidden; }
  .card-front { left: 219px; top: 50px; width: 774px; height: 472px; background: var(--paper); }
  .card-back { left: 217px; top: 568px; width: 777px; height: 456px; background: var(--sun); }

  .brand {
    position: absolute; display: flex; align-items: center; gap: 12px;
    color: var(--navy); font-weight: 700; line-height: 1.1;
  }
  .brand-dot { flex: none; border-radius: 50%; background: var(--navy); }
  .brand-front { left: 128px; top: 218px; font-size: 22px; width: 260px; }
  .brand-front .brand-dot { width: 22px; height: 22px; }
  .brand-back { left: 0; right: 0; top: 178px; justify-content: center; font-size: 46px; }
  .brand-back .brand-dot { width: 40px; height: 40px; }

  .divider { position: absolute; left: 392px; top: 162px; width: 2px; height: 204px; background: var(--navy); }

  .contact { position: absolute; left: 405px; top: 158px; color: var(--ink); }
  .person-name { font-size: 29px; font-weight: 600; color: var(--navy); line-height: 1.1; }
  .person-role { font-size: 18px; font-weight: 500; margin-top: 6px; }
  .address { font-size: 18px; font-weight: 500; line-height: 23px; margin-top: 14px; }
  .details { list-style: none; margin-top: 14px; }
  .details li { display: flex; align-items: center; gap: 10px; font-size: 18px; font-weight: 500; height: 28px; }
  .details svg { width: 18px; height: 18px; flex: none; }

  .band { position: absolute; left: 0; bottom: 0; width: 774px; height: 27px; }
</style>
</head>
<body>
<main class="canvas">
  <section class="card card-front">
    <div class="brand brand-front">
      <span class="brand-dot"></span>
      <span>Frostvale Harborline LLC</span>
    </div>
    <div class="divider"></div>
    <div class="contact">
      <h1 class="person-name">Daniel Harper</h1>
      <p class="person-role">Managing Director</p>
      <p class="address">48 Harbor Lane,<br>Ashford, NY 13901</p>
      <ul class="details">
        <li>
          <svg viewBox="0 0 18 18"><rect x="4" y="1" width="10" height="16" rx="2" fill="none" stroke="var(--sun)" stroke-width="2"/><circle cx="9" cy="14" r="1" fill="var(--sun)"/></svg>
          +52 1 (555) 014-2289
        </li>
        <li>
          <svg viewBox="0 0 18 18"><rect x="1" y="4" width="16" height="11" fill="var(--sun)"/><path d="M1 4 L9 10 L17 4" fill="none" stroke="#fff" stroke-width="1.4"/></svg>
          info@frostvaleharbor.com
        </li>
        <li>
          <svg viewBox="0 0 18 18"><circle cx="9" cy="9" r="8" fill="var(--sun)"/><path d="M1 9 H17 M9 1 C5 5 5 13 9 17 M9 1 C13 5 13 13 9 17" fill="none" stroke="#fff" stroke-width="1.2"/></svg>
          www.frostvaleharbor.com
        </li>
      </ul>
    </div>
    <svg class="band" viewBox="0 0 774 27" preserveAspectRatio="none">
      <rect x="0" y="0" width="774" height="27" fill="var(--sun)"/>
      <polygon points="0,0 254,0 227,27 0,27" fill="var(--navy)"/>
      <polygon points="254,0 262,0 235,27 227,27" fill="#fff"/>
      <polygon points="266,0 520,0 493,27 239,27" fill="var(--sky)"/>
      <polygon points="520,0 528,0 501,27 493,27" fill="#fff"/>
    </svg>
  </section>

  <section class="card card-back">
    <div class="brand brand-back">
      <span class="brand-dot"></span>
      <span>Frostvale Harborline LLC</span>
    </div>
  </section>
</main>
</body>
</html>
```